Animal Eye Clinic needs a Business card

We are a new veterinary ophthalmology practice (Ridgeline Pet Vision Care) and we need a business card designed. We only see animal eyes - we are not a regular veterinary clinic. We already have a logo. We are looking for a professional, good looking business card to hand out to our clients. We are looking for something simple but professional and contemporary. Our logo is likely the only picture/graphic that needs to be on the card.
Updates

Contact Information for Business Card

Delia Vossman, BSc, DVM, MSc, DipACVO
Veterinary Ophthalmologist

Phone: 250.418.3927
Email: ridgelinepetvisioncare@mailbox-example.net
Website: ridgelinepetvisioncare-example.net
Address: 1874 Thornbury Rd
Kelowna, BC, V1X 4M9

Colors

Designer to choose colors to be used in the design.

Requirements
Must have
• Our logo (attached)

```html
<!DOCTYPE html>
<html lang="en">
<head>
<meta charset="utf-8">
<title>Ridgeline Pet Vision Care — Business Card</title>
<link rel="stylesheet" href="https://fonts.googleapis.com/css2?family=Oswald:wght@500&family=Roboto:wght@300;400;500&display=swap">
<style>
  :root {
    --backdrop: #303030;
    --card: #262626;
    --teal: #12a0ae;
    --ink: #f2f2f2;
    --rule: #8a8a8a;
  }
  * { box-sizing: border-box; margin: 0; padding: 0; }
  html, body {
    width: 1200px; height: 901px; overflow: hidden;
    background: var(--backdrop);
  }
  .stage {
    width: 1200px; height: 901px;
    display: flex; flex-direction: column; align-items: center; justify-content: center;
    gap: 44px;
  }
  .card {
    position: relative;
    width: 640px; height: 366px;
    background: var(--card);
    box-shadow: 0 12px 30px rgba(0,0,0,0.45);
    overflow: hidden;
  }
  /* Front */
  .card-front {
    display: flex; align-items: center; justify-content: center;
  }
  .brand {
    display: flex; align-items: center; gap: 16px;
  }
  .brand-dot {
    width: 44px; height: 44px; border-radius: 50%;
    background: var(--teal);
  }
  .brand-name {
    font-family: "Roboto", sans-serif;
    font-weight: 500;
    font-size: 30px;
    letter-spacing: 0.5px;
    text-transform: uppercase;
    color: var(--teal);
  }
  /* Back */
  .card-back {
    display: flex; align-items: center; justify-content: center;
    padding-bottom: 20px;
  }
  .identity {
    width: 300px;
    text-align: right;
    padding-right: 16px;
  }
  .holder-name {
    font-family: "Oswald", sans-serif;
    font-weight: 500;
    font-size: 17px;
    color: var(--teal);
    text-transform: uppercase;
    line-height: 1.3;
  }
  .holder-role, .holder-address {
    font-family: "Roboto", sans-serif;
    font-weight: 300;
    font-size: 14.5px;
    color: var(--ink);
    line-height: 1.5;
  }
  .divider {
    width: 1px; height: 92px; background: var(--rule);
  }
  .contact {
    list-style: none;
    width: 300px;
    padding-left: 16px;
    font-family: "Roboto", sans-serif;
    font-weight: 300;
    font-size: 12.5px;
    color: var(--ink);
  }
  .contact li {
    display: flex; align-items: center; gap: 8px;
    line-height: 1.95;
    white-space: nowrap;
  }
  .contact svg { width: 12px; height: 12px; flex: none; fill: var(--teal); }
  .contact .accent { color: var(--teal); }
  .base-band {
    position: absolute; left: 0; right: 0; bottom: 0;
    height: 9px; background: var(--teal);
  }
</style>
</head>
<body>
<main class="stage">
  <section class="card card-front" aria-label="Card front">
    <div class="brand">
      <span class="brand-dot"></span>
      <span class="brand-name">Ridgeline Pet Vision Care</span>
    </div>
  </section>

  <section class="card card-back" aria-label="Card back">
    <div class="identity">
      <p class="holder-name">Delia Vossman, BSc, DVM, MSc, DipACVO</p>
      <p class="holder-role">Veterinary Ophthalmologist</p>
      <p class="holder-address">1874 Thornbury Rd, Kelowna, BC, V1X 4M9</p>
    </div>
    <div class="divider"></div>
    <ul class="contact">
      <li>
        <svg viewBox="0 0 24 24" aria-hidden="true"><path d="M6.6 10.8a15.1 15.1 0 0 0 6.6 6.6l2.2-2.2a1 1 0 0 1 1-.25 11.4 11.4 0 0 0 3.6.57 1 1 0 0 1 1 1V20a1 1 0 0 1-1 1A17 17 0 0 1 3 4a1 1 0 0 1 1-1h3.5a1 1 0 0 1 1 1c0 1.25.2 2.45.57 3.57a1 1 0 0 1-.25 1z"/></svg>
        <span>250.418.3927</span>
      </li>
      <li>
        <svg viewBox="0 0 24 24" aria-hidden="true"><path d="M2 5h20v14H2z M2 5l10 8 10-8" /></svg>
        <span>ridgelinepetvisioncare@mailbox-example.net</span>
      </li>
      <li>
        <svg viewBox="0 0 24 24" aria-hidden="true"><circle cx="12" cy="12" r="10"/></svg>
        <span>www.<span class="accent">ridgelinepetvisioncare-example</span>.net</span>
      </li>
    </ul>
    <div class="base-band"></div>
  </section>
</main>
</body>
</html>
```